Small legal and financial translation company needs Squarespace website, brochure and logo

Hello,
We are Lumarin Services (www.lumarinservices-example.com), a boutique legal and financial translation company. We offer our services mainly to Spanish customers. Our primary line of business is the translation of financial statements, but we translate a wide variety legal and financial texts.
The project we are offering comprises three parts: a redo of the current website, an informational brochure for potential customer and a logo design. These three parts should provide a consistent image. We would develop content soon.
We are looking for a website that would look like a typical law firm website, nothing too fancy. Right now, it is in English, Spanish and French, although the new site need only be in English and Spanish. There must be good toggling between the English and Spanish versions. There would be no need for tie-ins to social media and it would not contain a blog. Basically, a static site. We aren't interesting in driving traffic to the site or SEO, as we will contact nearly all potential customers beforehand. The website must be built in Squarespace to enable a smooth transition. The content would be similar to the current page, we'll be working on the exact content, but a rough draft is attached.
The brochure will be some three pages and would introduce the company to potential customers, using similar images as the website and the logo to be designed.
The only specifications for the logo is, as the website and brochure, it convey a sense of security and trust.
Feel free to ask with any questions as this is the first time we have used this platform.
Thank you!
Updates

I've added a more or less final version for the text in the brochure and updated the brief. Added Wednesday, June 10, 2015

Target Market(s)

Spanish law firms, auditors, accountants, banks, investment firms

Industry/Entity Type

Finance

Logo Text

Lumarin Services

Number of Pages Required

5+ page

Font styles to use
Serif

Requirements
Must have
• The website must be built in Squarespace and have a good option to toggle between English and Spanish versions.
• Brochure must be in both English and Spanish, I'm attaching a rough draft of the information that it will probably have. This should give an idea about what to include and the spacing. I will update it to include the final information.
Nice to have
• Would be nice to have some quality finance- and legal-related images
Should not have
• Vibrant colours

```html
<!DOCTYPE html>
<html lang="en">
<head>
<meta charset="utf-8">
<title>Lumarin Services – Legal &amp; Financial Translation</title>
<link rel="stylesheet" href="https://fonts.googleapis.com/css2?family=Cinzel:wght@400;500&family=EB+Garamond:wght@400&display=swap">
<style>
  :root {
    --backdrop: #cfcfcf;
    --paper: #ffffff;
    --navy: #283f7c;
    --ink: #000000;
    --body-text: #2a2a2a;
    --photo-light: #eeeeee;
    --photo-mid: #bdbdbd;
    --photo-dark: #6f6f6f;
  }
  * { margin: 0; padding: 0; box-sizing: border-box; }
  html, body {
    width: 1200px;
    height: 1200px;
    overflow: hidden;
    background: var(--backdrop);
  }
  .brochure-page {
    position: absolute;
    left: 268px;
    top: 110px;
    width: 699px;
    height: 991px;
    background: var(--paper);
    overflow: hidden;
  }
  .page-graphics {
    position: absolute;
    inset: 0;
    width: 699px;
    height: 991px;
  }
  .service {
    position: absolute;
    left: 38px;
    width: 615px;
  }
  .service--legal { top: 536px; }
  .service--financial { top: 703px; }
  .service-title {
    font-family: "Cinzel", serif;
    font-weight: 500;
    font-size: 32px;
    letter-spacing: 0.5px;
    color: var(--navy);
    line-height: 1;
  }
  .service-text {
    margin-top: 22px;
    font-family: "EB Garamond", serif;
    font-size: 13.4px;
    line-height: 19.5px;
    color: var(--body-text);
  }
  .service--legal .service-text { padding-left: 6px; }
  .site-address {
    position: absolute;
    left: 24px;
    top: 953px;
    font-family: "EB Garamond", serif;
    font-size: 18px;
    color: var(--paper);
  }
</style>
</head>
<body>
  <main class="brochure-page">
    <svg class="page-graphics" viewBox="0 0 699 991" xmlns="http://www.w3.org/2000/svg">
      <defs>
        <linearGradient id="photoTone" x1="0" y1="0" x2="1" y2="1">
          <stop offset="0" stop-color="var(--photo-mid)"/>
          <stop offset="0.45" stop-color="var(--photo-dark)"/>
          <stop offset="0.75" stop-color="var(--photo-light)"/>
          <stop offset="1" stop-color="var(--photo-light)"/>
        </linearGradient>
      </defs>
      <polygon class="header-photo" role="img"
        aria-label="Black and white photograph of a businessman signing a contract with a pen at a desk, keyboard and coffee cup behind"
        points="0,0 699,0 699,446 600,452 0,366" fill="url(#photoTone)"/>

      <g class="header-bands">
        <polygon class="band band--navy-accent" points="656,326 656,370 552,383" fill="var(--navy)"/>
        <polygon class="band band--black" points="364,412 699,366 699,445 617,448" fill="var(--ink)"/>
        <polygon class="band band--navy" points="0,366 600,452 0,477" fill="var(--navy)"/>
        <line x1="0" y1="364" x2="600" y2="451" stroke="var(--paper)" stroke-width="2"/>
      </g>

      <g class="footer-bands">
        <polygon class="band band--navy-accent" points="660,880 673,923 532,937" fill="var(--navy)"/>
        <polygon class="band band--black" points="364,957 699,923 699,991 560,991" fill="var(--ink)"/>
        <polygon class="band band--navy" points="0,923 699,989 699,991 0,991" fill="var(--navy)"/>
        <line x1="360" y1="958" x2="699" y2="924" stroke="var(--paper)" stroke-width="2"/>
      </g>
    </svg>

    <section class="service service--legal">
      <h2 class="service-title">Legal Translation</h2>
      <p class="service-text">Legal translation includes but is not limited to: all manner of deeds; contracts; due diligence; bylaws; expert reports; lawsuits; appeals; loan agreements; powers of attorney; judgments and court orders; M&amp;A agreements; LBOs</p>
    </section>

    <section class="service service--financial">
      <h2 class="service-title">Financial Translation</h2>
      <p class="service-text">Financial translation includes but is not limited to: financial statements and notes to the financial statements; annual reports; auditor’s reports; director’s reports; limited reviews; business plans; macroeconomic reports; investment fund reports; annual banking reports; financing agreements</p>
    </section>

    <p class="site-address">www.lumarinservices-example.com</p>
  </main>
</body>
</html>
```